Vosley Insurance Stationery Design Project

We need a stationery design for business cards, letterhead and envelopes.

Please refer to attached brief for further information.

Industry/Entity Type

Business

```html
<!DOCTYPE html>
<html lang="en">
<head>
<meta charset="utf-8">
<title>Vosley Insurance Stationery</title>
<link href="https://fonts.googleapis.com/css2?family=Mulish:wght@400;600;700&display=swap" rel="stylesheet">
<style>
  :root {
    --navy: #14364c;
    --orange: #f47a20;
    --backdrop: #e2e2e2;
    --paper: #ffffff;
    --pale: #c9d3da;
  }
  * { margin: 0; padding: 0; box-sizing: border-box; }
  html, body { width: 1200px; height: 900px; overflow: hidden; }
  body {
    background: var(--backdrop);
    font-family: "Mulish", Arial, sans-serif;
    color: var(--navy);
    position: relative;
  }
  .sheet { position: absolute; background: var(--paper); box-shadow: 0 1px 5px rgba(0,0,0,.25); overflow: hidden; }

  .brand { position: absolute; display: flex; align-items: center; white-space: nowrap; }
  .brand-dot { border-radius: 50%; background: var(--orange); flex: none; }
  .brand-name { font-weight: 700; color: var(--navy); letter-spacing: -.2px; }
  .tagline { position: absolute; font-weight: 700; white-space: nowrap; }

  /* Letterhead */
  .letterhead { left: 84px; top: 58px; width: 612px; height: 793px; }
  .letterhead .brand { left: 36px; top: 38px; gap: 10px; }
  .letterhead .brand-dot { width: 15px; height: 15px; }
  .letterhead .brand-name { font-size: 30px; }
  .letterhead .tagline { left: 52px; top: 94px; font-size: 10.5px; }
  .letterhead-contact { position: absolute; right: 23px; top: 36px; text-align: right; font-size: 9px; line-height: 12.2px; }
  .letterhead-contact .gap { height: 4px; }
  .web { color: var(--orange); font-weight: 700; }
  .letterhead-footer { position: absolute; left: 0; bottom: 0; width: 100%; height: 56px; background: var(--navy); border-top: 4px solid var(--orange); color: #fff; text-align: center; font-size: 6.3px; line-height: 7.6px; padding-top: 4px; }
  .letterhead-footer .copyright { font-weight: 700; margin-top: 3px; display: flex; justify-content: center; align-items: center; gap: 5px; }
  .letterhead-footer .copyright i { width: 6px; height: 6px; border-radius: 50%; background: var(--orange); display: inline-block; }

  /* Business card back */
  .card-back { left: 822px; top: 126px; width: 252px; height: 144px; background: var(--navy); }
  .card-back .brand { left: 50px; top: 58px; gap: 7px; }
  .card-back .brand-dot { width: 9px; height: 9px; }
  .card-back .brand-name { font-size: 19px; color: #fff; }
  .card-back .legal { position: absolute; left: 0; right: 0; top: 120px; text-align: center; color: var(--pale); font-size: 4.2px; line-height: 5.3px; }

  /* Business card front */
  .card-front { left: 697px; top: 291px; width: 251px; height: 145px; }
  .card-front .brand { left: 8px; top: 9px; gap: 5px; }
  .card-front .brand-dot { width: 7px; height: 7px; }
  .card-front .brand-name { font-size: 15px; }
  .card-front .tagline { left: 16px; top: 38px; font-size: 6.4px; }
  .card-front .web { position: absolute; right: 12px; top: 18px; font-size: 7px; }
  .card-person { position: absolute; left: 16px; top: 60px; }
  .card-person .name { font-size: 9.5px; font-weight: 700; }
  .card-person .role { font-size: 7px; font-weight: 700; color: var(--orange); }
  .card-address { position: absolute; left: 16px; top: 93px; font-size: 5.6px; line-height: 7.2px; }
  .card-contact { position: absolute; left: 116px; top: 94px; font-size: 5.6px; line-height: 7.2px; list-style: none; }
  .card-contact li { display: flex; align-items: center; gap: 3px; }
  .card-contact svg { width: 5px; height: 5px; fill: var(--navy); }
  .card-band { position: absolute; left: 0; bottom: 0; width: 100%; height: 17px; background: var(--navy); border-top: 3px solid var(--orange); }

  /* Envelope */
  .envelope { left: 476px; top: 479px; width: 685px; height: 297px; }
  .envelope .brand { left: 38px; top: 22px; gap: 10px; }
  .envelope .brand-dot { width: 15px; height: 15px; }
  .envelope .brand-name { font-size: 30px; }
  .envelope .tagline { left: 39px; top: 77px; font-size: 10px; }
  .return-address { position: absolute; left: 464px; top: 40px; font-size: 10.5px; line-height: 13px; }
  .return-address strong { font-weight: 700; }
  .envelope-band { position: absolute; left: 0; bottom: 0; width: 100%; height: 27px; background: var(--navy); border-top: 6px solid var(--orange); }
</style>
</head>
<body>

<section class="sheet letterhead">
  <div class="brand"><span class="brand-dot"></span><span class="brand-name">Vosley Insurance</span></div>
  <p class="tagline">Business and Life Insurance Brokers and Advisers</p>
  <address class="letterhead-contact" style="font-style:normal">
    Level 4, 18 Harlow St<br>Eastwood Park NSW 2081<br>PO Box 417<br>Eastwood Park NSW 2080
    <div class="gap"></div>
    Ph: (02) 5550 1824<br>Fax: (02) 5550 1890<br>Email: info@vosleyinsurance.com.au<br>
    <span class="web">www.vosleyinsurance.com.au</span>
  </address>
  <footer class="letterhead-footer">
    Vosley Insurance Holdings Pty Ltd ABN 41 902 115 674 is an Authorised Representative of Harbourline Advice Australia Pty Limited<br>
    Authorised Representative No. 402117 &nbsp;|&nbsp; Australian Financial Services No. 250318<br>
    Harbourline Financial Services Pty Ltd and its advisers are members of Crestway Financial<br>
    Advisers and Authorised Representatives of Norland Advice Group Pty Ltd AFSL 238811
    <div class="copyright"><i></i>Copyright 2012 Vosley Insurance Holdings Pty Ltd. All rights reserved.</div>
  </footer>
</section>

<section class="sheet card-back">
  <div class="brand"><span class="brand-dot"></span><span class="brand-name">Vosley Insurance</span></div>
  <p class="legal">
    Authorised Representative No. 402117 &nbsp;|&nbsp; Harbourline Advice Pty Ltd AFSL 250318<br>
    Harbourline Financial Services Pty Ltd and its advisers are members of Crestway Financial Advisers<br>
    and Authorised Representatives of Norland Advice Group Pty Ltd AFSL 238811
  </p>
</section>

<section class="sheet card-front">
  <div class="brand"><span class="brand-dot"></span><span class="brand-name">Vosley Insurance</span></div>
  <span class="web">www.vosleyinsurance.com.au</span>
  <p class="tagline">Business and Life Insurance Brokers and Advisers</p>
  <div class="card-person"><p class="name">Mark Hollis</p><p class="role">Director</p></div>
  <address class="card-address" style="font-style:normal">Level 4, 18 Harlow St<br>Eastwood Park NSW 2081<br>PO Box 417<br>Eastwood Park NSW 2080</address>
  <ul class="card-contact">
    <li><svg viewBox="0 0 10 10"><path d="M2 0h2l1 3-1.5 1a6 6 0 0 0 2.5 2.5L7 5l3 1v2a2 2 0 0 1-2 2A8 8 0 0 1 0 2a2 2 0 0 1 2-2z"/></svg>(02) 5550 1824</li>
    <li><svg viewBox="0 0 10 10"><rect x="0" y="3" width="10" height="5" rx="1"/><rect x="2" y="0" width="6" height="3"/></svg>(02) 5550 1890</li>
    <li><svg viewBox="0 0 10 10"><rect x="2" y="0" width="6" height="10" rx="1"/></svg>0400 555 219</li>
    <li><svg viewBox="0 0 10 10"><rect x="0" y="2" width="10" height="6" rx="1"/></svg>mhollis@harbourline.net.au</li>
  </ul>
  <div class="card-band"></div>
</section>

<section class="sheet envelope">
  <div class="brand"><span class="brand-dot"></span><span class="brand-name">Vosley Insurance</span></div>
  <p class="tagline">Business and Life Insurance Brokers and Advisers</p>
  <address class="return-address" style="font-style:normal"><strong>Vosley Insurance Holdings Pty Ltd</strong><br>PO Box 417<br>Eastwood Park NSW 2080</address>
  <div class="envelope-band"></div>
</section>

</body>
</html>
```